Working Capital graphics

Our business advisory firm requires 9 images to be re-created and improved in the branding of our business.

The 9 images have been uploaded below and the colours and branding of the business can be found at the website www.tallowmereadvisory.com.au

```html
<!DOCTYPE html>
<html lang="en">
<head>
<meta charset="utf-8">
<title>Working Capital</title>
<link rel="stylesheet" href="https://fonts.googleapis.com/css2?family=Quicksand:wght@600;700&display=swap">
<style>
  :root {
    --brand-orange: #f5901e;
    --brand-blue: #12a5e6;
    --ink: #333333;
    --frame-dark: #3d3d3d;
    --paper: #ffffff;
    --tile-size: 120px;
  }
  * { margin: 0; padding: 0; box-sizing: border-box; }
  html, body { width: 1200px; height: 569px; overflow: hidden; background: var(--paper); }
  .canvas {
    position: relative;
    width: 1200px;
    height: 569px;
    font-family: "Quicksand", sans-serif;
    color: var(--ink);
  }
  .title {
    position: absolute;
    top: 88px;
    left: 0;
    width: 100%;
    text-align: center;
    font-size: 43px;
    font-weight: 700;
    letter-spacing: 0.3px;
  }
  .title .accent-orange { color: var(--brand-orange); }
  .title .accent-blue { color: var(--brand-blue); }

  .factor {
    position: absolute;
    width: 0;
    height: 0;
  }
  .factor .tile {
    position: absolute;
    left: calc(var(--tile-size) / -2);
    top: calc(var(--tile-size) / -2);
    width: var(--tile-size);
    height: var(--tile-size);
    border-radius: 16px;
    border: 1px solid;
    background: var(--paper);
    transform: rotate(45deg);
  }
  .factor .label {
    position: absolute;
    left: -80px;
    width: 160px;
    transform: translateY(-50%);
    text-align: center;
    font-size: 15.5px;
    font-weight: 600;
    line-height: 22px;
  }
  .factor--upper { z-index: 1; }
  .factor--lower { z-index: 2; }
  .factor--blue .tile { border-color: var(--brand-blue); }
  .factor--orange .tile { border-color: var(--brand-orange); }
  .factor--lower .tile {
    border-color: var(--frame-dark);
    box-shadow: 2px 2px 5px rgba(0, 0, 0, 0.12);
  }
</style>
</head>
<body>
<main class="canvas">
  <h1 class="title"><span class="accent-orange">Working</span> <span class="accent-blue">Capital</span></h1>

  <div class="factor factor--upper factor--blue" style="left:221px; top:268px;">
    <div class="tile"></div><p class="label">Supply<br>Chain Issues</p>
  </div>
  <div class="factor factor--upper factor--orange" style="left:408px; top:268px;">
    <div class="tile"></div><p class="label">Forecasting<br>And<br>Planning</p>
  </div>
  <div class="factor factor--upper factor--blue" style="left:595px; top:268px;">
    <div class="tile"></div><p class="label">SKU<br>Complexity</p>
  </div>
  <div class="factor factor--upper factor--orange" style="left:782px; top:268px;">
    <div class="tile"></div><p class="label">KPIs<br>Measures</p>
  </div>
  <div class="factor factor--upper factor--blue" style="left:970px; top:268px;">
    <div class="tile"></div><p class="label">Terms &amp;<br>Conditions</p>
  </div>

  <div class="factor factor--lower" style="left:314px; top:380px;">
    <div class="tile"></div><p class="label">Process<br>Issues</p>
  </div>
  <div class="factor factor--lower" style="left:501px; top:380px;">
    <div class="tile"></div><p class="label">Customer<br>Management</p>
  </div>
  <div class="factor factor--lower" style="left:688px; top:380px;">
    <div class="tile"></div><p class="label">Supplier<br>Management</p>
  </div>
  <div class="factor factor--lower" style="left:875px; top:380px;">
    <div class="tile"></div><p class="label">IT Systems<br>&amp; Information</p>
  </div>
</main>
</body>
</html>
```